Brightway Coordination Group Business card

We wish to have a professional Business card to present to large Corporate CEO's ASAP.

Our web site helps explain our business www.brightwaycg.org

Brightway Coordination Group was established after we discovered how difficult it is to organise outsourced services while heading up a business or company.

We act as a facilitator for businesses who don't have the desire, expertise or recourses to manage their own systems and meet all their requirements.

We provide an all in one facility management solution for all types of businesses. We manage schedules, contractors and costs on behalf of businesses and their needs and wants.

Having an extensive network ensures we are able to connect businesses with the right service providers.

Target Market(s)

Company CEO

Industry/Entity Type

Business

Font styles to use
Sans Serif

Colors
33a6d7
f9fdfe
0355a3

Requirements
Must have
• professional design
Nice to have
• colours to match logo

```html
<!DOCTYPE html>
<html lang="en">
<head>
<meta charset="utf-8">
<title>Brightway Coordination Group – Business Card</title>
<link rel="stylesheet" href="https://fonts.googleapis.com/css2?family=Raleway:wght@300;400;700&family=Lato:wght@400;700&display=swap">
<style>
  :root {
    --stage: #2b2b2d;
    --brand-blue: #0355a3;
    --brand-blue-deep: #003f80;
    --brand-sky: #33a6d7;
    --paper: #f9fdfe;
    --paper-shade: #e4e6e8;
    --ink: #1c1c1e;
    --band: #1f1f21;
    --band-text: #d8d8d8;
  }
  * { box-sizing: border-box; margin: 0; padding: 0; }
  html, body { width: 1200px; height: 997px; overflow: hidden; }
  body {
    background: var(--stage);
    font-family: "Lato", sans-serif;
    position: relative;
  }
  .card {
    position: absolute;
    left: 280px;
    width: 640px;
    height: 366px;
    border-radius: 28px;
    overflow: hidden;
    box-shadow: 0 14px 30px rgba(0,0,0,.45);
  }
  /* back side */
  .card--back {
    top: 70px;
    background: linear-gradient(160deg, #1a6fc0 0%, var(--brand-blue) 55%, var(--brand-blue-deep) 100%);
  }
  .back-name {
    position: absolute;
    right: 40px;
    bottom: 120px;
    text-align: right;
    color: var(--ink);
    font-family: "Raleway", sans-serif;
    font-weight: 700;
    text-transform: uppercase;
  }
  .back-name__tag { font-size: 13px; letter-spacing: 1px; }
  .back-name__title { font-size: 24px; letter-spacing: 1px; margin-top: 4px; }

  /* front side */
  .card--front {
    top: 520px;
    background: linear-gradient(135deg, #ffffff 0%, var(--paper) 45%, var(--paper-shade) 100%);
  }
  .front-brand {
    position: absolute;
    left: 150px;
    top: 82px;
    display: flex;
    align-items: center;
    gap: 14px;
  }
  .front-brand__dot {
    width: 40px; height: 40px;
    border-radius: 50%;
    background: var(--brand-blue);
  }
  .front-brand__name {
    font-family: "Raleway", sans-serif;
    font-weight: 700;
    font-size: 21px;
    letter-spacing: 1px;
    text-transform: uppercase;
    color: var(--ink);
  }
  .name-band {
    position: absolute;
    right: 0;
    top: 150px;
    width: 300px;
    height: 54px;
    background: var(--band);
    display: flex;
    align-items: center;
    padding-left: 30px;
    font-family: "Raleway", sans-serif;
    font-size: 21px;
    letter-spacing: 1px;
    text-transform: uppercase;
    color: var(--band-text);
  }
  .name-band__first { font-weight: 300; margin-right: 7px; }
  .name-band__last { font-weight: 400; color: #ffffff; }
  .contact-shape { position: absolute; left: 0; top: 0; }
  .contact-list {
    position: absolute;
    left: 26px;
    top: 248px;
    list-style: none;
    color: #ffffff;
    font-size: 14px;
  }
  .contact-list li {
    display: flex;
    align-items: center;
    gap: 12px;
    height: 22px;
  }
  .contact-list svg { width: 14px; height: 14px; fill: #ffffff; }
</style>
</head>
<body>

  <section class="card card--back" aria-label="Card back">
    <div class="back-name">
      <p class="back-name__tag">Coordination Group</p>
      <p class="back-name__title">Brightway Coordination Group</p>
    </div>
  </section>

  <section class="card card--front" aria-label="Card front">
    <svg class="contact-shape" width="640" height="366" viewBox="0 0 640 366" aria-hidden="true">
      <path d="M0 232 H370 Q400 232 400 262 V320 H0 Z" fill="var(--brand-blue)"/>
      <path d="M-2 238 H366 Q392 238 392 264 V312 H-2" fill="none" stroke="#ffffff" stroke-width="2.5"/>
      <rect x="0" y="326" width="640" height="8" fill="var(--brand-blue)"/>
    </svg>

    <div class="front-brand">
      <span class="front-brand__dot"></span>
      <span class="front-brand__name">Brightway Coordination Group</span>
    </div>

    <div class="name-band">
      <span class="name-band__first">Daniel</span>
      <span class="name-band__last">Whitford</span>
    </div>

    <ul class="contact-list">
      <li>
        <svg viewBox="0 0 16 16"><path d="M3 2h3l1 3-2 1c1 2 2 3 4 4l1-2 3 1v3c0 1-1 2-2 2C6 14 2 10 2 4c0-1 0-2 1-2z"/></svg>
        0400 218 574
      </li>
      <li>
        <svg viewBox="0 0 16 16"><path d="M6 10l4-4 1 1-4 4zM4 12a2 2 0 0 1 0-3l2-2 1 1-2 2a1 1 0 0 0 1 1l2-2 1 1-2 2a2 2 0 0 1-3 0zM12 4a2 2 0 0 1 0 3l-2 2-1-1 2-2a1 1 0 0 0-1-1L8 7 7 6l2-2a2 2 0 0 1 3 0z"/></svg>
        www.brightwaycg.org
      </li>
      <li>
        <svg viewBox="0 0 16 16"><path d="M1 4h14v9H1zM2 5l6 4 6-4v-.5H2z" fill-rule="evenodd"/></svg>
        daniel@brightwaycg.org
      </li>
    </ul>
  </section>

</body>
</html>
```